Business cards for Norwegian software consultancy business

We are in need of business cards for our Norwegian consultancy company.
“Valto Brindex AS” specializes in software development, architecture and agile methodology, providing mostly on-site services at customers.
The cards should reflect a certain level of business professionalism with an elegant touch, while paying tribute to our modern and technological heritage. Our logo should be featured, as well as room for basic information about the cardholder and legal information of the company (company name, address and VAT number).
We would like our cards to reflect that we are a modern consulting company. It should present a professional image that people will remember. The texture and color pallette should reflect our professionalism and reliability, so we prefer a light color pallette with colors such as gray, white, blue and black. The number of colors used should however not be overwhelming, with the text being distinct and readable.
We are open to untraditional layouts and playful designs as long as they communicate the intent stated above.
You could also take a look at our website http://www.brindex.no for input on our visual profile.
Our logo is attached in the form of vectors and rasterized PNG. Please comment if you would like the black-white and/or inverted versions as well.
Industry/Entity Type
Architecture
Contact Information for Business Card
Company information:
Valto Brindex AS
Kvernlia 14, 3170 Sem
482 71 519
info@brindex.no
www.brindex.no
Employee information:
Full name
Title
Email
Phone
Font styles to use
Look and feel

```html
<!DOCTYPE html>
<html lang="no">
<head>
<meta charset="utf-8">
<title>Valto Brindex AS – Business Cards</title>
<link rel="stylesheet" href="https://fonts.googleapis.com/css2?family=Lato:wght@400;700&display=swap">
<style>
  :root {
    --backdrop: #cfcfcd;
    --card-dark: #232624;
    --card-light: #f7f7f6;
    --ink: #1f2221;
    --accent-blue: #4f86b9;
    --white: #ffffff;
  }
  * { margin: 0; padding: 0; box-sizing: border-box; }
  html, body { width: 1200px; height: 900px; overflow: hidden; }
  body {
    background: var(--backdrop);
    font-family: "Lato", sans-serif;
    position: relative;
  }
  .card {
    position: absolute;
    left: 320px;
    width: 560px;
    height: 320px;
    border-radius: 3px;
    overflow: hidden;
    box-shadow: 0 6px 18px rgba(0,0,0,0.18);
  }

  /* Back side */
  .card-back { top: 100px; background: var(--card-dark); }
  .card-back .brand {
    position: absolute; left: 0; right: 0; top: 118px;
    display: flex; justify-content: center; align-items: center; gap: 14px;
  }
  .brand-square { width: 22px; height: 22px; background: var(--accent-blue); }
  .card-back .brand-name {
    color: var(--white); font-size: 34px; font-weight: 400; letter-spacing: 4px;
  }
  .card-back .web {
    position: absolute; left: 0; right: 0; top: 212px; text-align: center;
    color: var(--white); font-size: 13px; letter-spacing: 3px;
  }

  /* Front side */
  .card-front { top: 480px; background: var(--card-light); }
  .card-front .brand {
    position: absolute; right: 34px; top: 36px;
    display: flex; align-items: center; gap: 12px;
  }
  .brand-divider { width: 1px; height: 44px; background: var(--ink); }
  .card-front .brand-name {
    color: var(--ink); font-size: 30px; font-weight: 400; letter-spacing: 3px;
  }
  .holder { position: absolute; left: 30px; top: 116px; }
  .holder-name { color: var(--accent-blue); font-size: 18px; font-weight: 400; line-height: 22px; }
  .holder-title { color: var(--ink); font-size: 11px; letter-spacing: 0.5px; margin-top: 2px; }
  .rule-line {
    position: absolute; left: 30px; right: 34px; top: 160px; height: 1px; background: var(--accent-blue);
  }
  .contact-list { position: absolute; left: 30px; top: 172px; list-style: none; }
  .contact-list li {
    display: flex; align-items: center; gap: 10px;
    color: var(--ink); font-size: 13px; line-height: 19px;
  }
  .contact-list svg { width: 11px; height: 11px; fill: none; stroke: var(--accent-blue); stroke-width: 1.4; }
  .company {
    position: absolute; right: 34px; top: 172px; text-align: right;
    color: var(--ink); font-size: 13px; line-height: 19px;
  }
  .company-name { font-weight: 700; }
  .footer-bands { position: absolute; left: 0; bottom: 0; width: 560px; height: 50px; }
  .footer-web {
    position: absolute; right: 34px; bottom: 6px;
    color: var(--white); font-size: 12px; letter-spacing: 2.5px; line-height: 16px;
  }
</style>
</head>
<body>

<section class="card card-back" aria-label="Card back">
  <div class="brand">
    <span class="brand-square"></span>
    <span class="brand-name">VALTO BRINDEX</span>
  </div>
  <p class="web">www.brindex.no</p>
</section>

<section class="card card-front" aria-label="Card front">
  <div class="brand">
    <span class="brand-square"></span>
    <span class="brand-divider"></span>
    <span class="brand-name">VALTO BRINDEX</span>
  </div>

  <div class="holder">
    <p class="holder-name">Henrik Solvang</p>
    <p class="holder-title">DIRECTOR</p>
  </div>

  <div class="rule-line"></div>

  <ul class="contact-list">
    <li>
      <svg viewBox="0 0 12 12"><path d="M2 1.5h2.5l1 2.5-1.5 1a6 6 0 0 0 3 3l1-1.5 2.5 1V10.5A1 1 0 0 1 9.5 11.5 8.5 8.5 0 0 1 1 3 1 1 0 0 1 2 1.5z"/></svg>
      482 71 519
    </li>
    <li>
      <svg viewBox="0 0 12 12"><rect x="3" y="1" width="6" height="3"/><rect x="1" y="4" width="10" height="5"/><rect x="3" y="7.5" width="6" height="3.5"/></svg>
      482 71 520
    </li>
    <li>
      <svg viewBox="0 0 12 12"><rect x="1" y="2.5" width="10" height="7"/><path d="M1 2.5l5 4 5-4"/></svg>
      hsolvang@brindex.no
    </li>
  </ul>

  <div class="company">
    <p class="company-name">Valto Brindex AS</p>
    <p>Kvernlia 14</p>
    <p>3170 Sem</p>
  </div>

  <svg class="footer-bands" viewBox="0 0 560 50" aria-hidden="true">
    <path d="M0 38 L318 28 L330 20 L560 20 L560 26 L334 26 L322 34 L0 44 Z" fill="var(--accent-blue)"/>
    <path d="M0 44 L322 34 L334 26 L560 26 L560 50 L0 50 Z" fill="var(--card-dark)"/>
  </svg>
  <p class="footer-web">www.brindex.no</p>
</section>

</body>
</html>
```